Web application layout remake

We are looking for a makeover on our web application called “KRVcrate” - it's a document management and digital archiving system integrating workflows and allowing you to free up physical space in your office currently occupied with documents by moving them to secure external custody.
We are expecting you to include the following:
• homepage
• signup page
• application page
This project is for the whole website (which is not big at all anyway!) and not just for the design of one page. The coding should be in HTML5 only.
We are aiming for fresh, appealing, clean, user friendly ,web 2.0, jquery layout.
Remakes or changes on the logo are welcome.
The application will be sold through the portal.
Please find in attachment the print screen of the application to aid you (this is the current view customers have after logging in but the layout is obsolete and we want a brand new!).
Reason: Still not happy with the received layouts. Keep up the good work! Thanks!
Reason: Still not happy with the whole solution and finding alternate app interfaces!

```html
<!DOCTYPE html>
<html lang="en">
<head>
<meta charset="utf-8">
<title>KRVcrate Application</title>
<link rel="stylesheet" href="https://fonts.googleapis.com/css2?family=Montserrat:wght@400;500&family=Open+Sans:wght@400;600;700&family=Roboto+Condensed:wght@700&display=swap">
<style>
  :root {
    --ink: #333333;
    --muted: #555555;
    --blue: #1a86d0;
    --blue-dark: #0d6fb4;
    --blue-light: #2ea3ea;
    --orange: #ff6a00;
    --dark: #1b1b1b;
    --panel: #f1f1f1;
    --bar: #f2f2f2;
    --line: #d6d6d6;
    --field: #ffffff;
    --footer: #e1e1e1;
    --white: #ffffff;
  }
  * { box-sizing: border-box; margin: 0; padding: 0; }
  html, body { width: 1200px; height: 1070px; overflow: hidden; background: var(--white); }
  body { font-family: "Open Sans", Arial, sans-serif; color: var(--ink); }
  .page { position: relative; width: 1000px; height: 892px; transform: scale(1.2); transform-origin: 0 0; }
  .abs { position: absolute; }

  /* header */
  .masthead { left: 0; top: 0; width: 1000px; height: 110px;
    background: radial-gradient(ellipse at 48% 30%, #4a3a35 0%, #2a2421 35%, #141414 75%); }
  .brand { left: 124px; top: 40px; display: flex; align-items: center; gap: 10px; }
  .brand-dot { width: 26px; height: 26px; border-radius: 50%; background: var(--white); }
  .brand-name { font-family: "Montserrat", sans-serif; font-weight: 500; font-size: 28px; color: var(--white); }
  .top-links { right: 116px; top: 14px; display: flex; align-items: center; font-size: 11px; color: var(--white); font-weight: 600; }
  .top-links span { display: flex; align-items: center; gap: 5px; padding: 0 10px; }
  .top-links .sep { width: 1px; height: 14px; background: #555; padding: 0; }
  .login { background: var(--orange); border-radius: 2px; padding: 3px 6px !important; margin-left: 8px; }
  .app-title { right: 116px; top: 58px; font-family: "Roboto Condensed", sans-serif; font-weight: 700; font-size: 25px; color: var(--white); }
  .app-title em { font-style: normal; color: var(--blue-light); }

  /* nav */
  .navbar { left: 0; top: 110px; width: 1000px; height: 58px; background: linear-gradient(#f7f7f7, #ececec); border-bottom: 1px solid var(--line); }
  .nav-item { top: 131px; font-size: 12px; font-weight: 700; color: #444; letter-spacing: .2px; }
  .nav-item.active { color: var(--blue); }
  .search { left: 743px; top: 129px; width: 141px; height: 21px; background: #e6e6e6; border: 1px solid #d8d8d8; display: flex; }
  .search span { flex: 1; font-size: 10px; color: #777; padding: 3px 5px; font-family: Georgia, serif; }
  .search i { width: 23px; border-left: 1px solid #ccc; display: flex; align-items: center; justify-content: center; }

  .dropdown { left: 463px; top: 168px; width: 171px; height: 83px; background: var(--dark); border-radius: 0 0 3px 3px; border: 1px solid #000; }
  .dropdown div { height: 23.5px; font-size: 10.5px; color: var(--white); padding: 12px 0 0 15px; border-bottom: 1px solid #3b3b3b; }
  .dropdown div:first-child { height: 31px; }
  .dropdown div:last-child { border-bottom: 0; }

  /* sidebar */
  .sidebar { left: 118px; top: 168px; width: 213px; height: 605px; background: var(--panel); border-left: 1px solid var(--line); border-right: 3px solid #bdbdbd; }
  .panel-head { left: 118px; width: 210px; height: 36px; background: linear-gradient(var(--blue-light), var(--blue-dark)); color: var(--white); font-family: "Montserrat", sans-serif; font-size: 14px; display: flex; align-items: center; gap: 8px; padding-left: 23px; }
  .tree { left: 146px; top: 224px; }
  .tree li { list-style: none; height: 22px; display: flex; align-items: center; gap: 3px; font-size: 11px; color: var(--blue-dark); }
  .tree-rail { left: 149px; top: 222px; width: 1px; height: 166px; background: #b9b9b9; }
  .empty-note { left: 141px; top: 524px; font-family: "Montserrat", sans-serif; font-size: 11px; color: var(--muted); }
  .note-rule { left: 141px; top: 551px; width: 164px; height: 1px; background: #dadada; }

  /* main */
  .crumb { left: 356px; top: 196px; font-size: 10.5px; color: var(--blue-dark); display: flex; align-items: center; gap: 6px; }
  .bar { left: 355px; width: 529px; height: 27px; background: var(--bar); font-size: 11px; font-weight: 600; color: #222; padding: 6px 0 0 16px; }
  .bar b { display: inline-block; width: 0; height: 0; border: 4px solid transparent; border-top: 5px solid #222; margin-left: 6px; vertical-align: -1px; }
  .label { left: 355px; font-size: 10px; color: #444; }
  .select { height: 17px; background: linear-gradient(#fafafa, #e8e8e8); border: 1px solid #bcbcbc; border-radius: 2px; font-size: 8px; color: #333; padding: 3px 0 0 6px; }
  .select::after { content: ""; position: absolute; right: 0; top: 0; width: 14px; height: 15px; border-left: 1px solid #bcbcbc;
    background: linear-gradient(to bottom, transparent 2px, transparent 2px); }
  .arrows { position: absolute; right: 4px; top: 3px; }
  .field { height: 17px; background: var(--field); border: 1px solid #bcbcbc; border-radius: 2px; }

  .pager { display: flex; align-items: center; gap: 6px; font-size: 8px; }
  .pg-btn { width: 16px; height: 17px; border: 1px solid #bcbcbc; background: linear-gradient(#fafafa, #e6e6e6); display: flex; align-items: center; justify-content: center; border-radius: 2px; }
  .go { font-size: 8px; color: #333; }

  .grid { left: 355px; top: 471px; width: 529px; border-collapse: collapse; font-size: 9px; }
  .grid th { background: var(--blue); color: var(--white); font-weight: 400; font-size: 11px; height: 26px; border-right: 1px solid #6fb5e6; }
  .grid th i { display: inline-block; border: 3px solid transparent; border-left: 4px solid #bfe0f7; margin-left: 5px; }
  .grid td { height: 31px; border: 1px solid var(--blue); border-top: 0; text-align: center; color: #222; }
  .grid td.tool { border-left: 1px solid #d0d0d0; border-right: 1px solid #d0d0d0; }
  .grid td.tool:last-child { border-right: 1px solid var(--blue); }

  /* footer */
  .footer { left: 0; top: 773px; width: 1000px; height: 119px; background: var(--footer); }
  .email { left: 118px; top: 797px; width: 156px; height: 24px; background: var(--field); border: 1px solid #c8c8c8; font-size: 10px; color: #666; padding: 5px 7px; }
  .send { left: 279px; top: 797px; width: 74px; height: 24px; background: var(--orange); color: var(--white); font-size: 10px; font-weight: 700; text-align: center; padding-top: 6px; letter-spacing: .3px; }
  .vrule { top: 795px; width: 1px; height: 28px; background: #c4c4c4; }
  .call { left: 450px; top: 796px; font-family: "Montserrat", sans-serif; font-size: 13px; color: #222; display: flex; align-items: baseline; gap: 7px; }
  .call strong { font-size: 18px; font-weight: 500; letter-spacing: .3px; }
  .social { width: 28px; height: 28px; top: 795px; border: 1.5px solid #444; border-radius: 50%; }
  .social.focus { border-color: var(--blue); }
  .foot-rule { left: 118px; top: 839px; width: 766px; height: 1px; background: #c9c9c9; }
  .foot-links { left: 118px; top: 853px; font-family: "Montserrat", sans-serif; font-size: 11px; color: #222; display: flex; gap: 9px; }
  .copyright { right: 116px; top: 853px; font-family: "Montserrat", sans-serif; font-size: 11px; color: #222; }
</style>
</head>
<body>
<div class="page">

  <header>
    <div class="abs masthead" role="img" aria-label="Dark blurred office photo background"></div>
    <div class="abs brand"><span class="brand-dot"></span><span class="brand-name">KRVcrate</span></div>
    <nav class="abs top-links">
      <span><svg width="11" height="10" viewBox="0 0 11 10"><path d="M1 5 5.5 1 10 5M2.5 4v5h6V4" fill="none" stroke="#fff" stroke-width="1.3"/></svg>Home</span>
      <span class="sep"></span>
      <span><svg width="10" height="10" viewBox="0 0 10 10"><path d="M1 5h6M5 3l2 2-2 2M7 1h2v8H7" fill="none" stroke="#fff" stroke-width="1.2"/></svg>Sign Up</span>
      <span class="login"><svg width="8" height="10" viewBox="0 0 8 10"><rect x="0.5" y="4.5" width="7" height="5" fill="#fff"/><path d="M2 4.5V3a2 2 0 0 1 4 0v1.5" fill="none" stroke="#fff" stroke-width="1.2"/></svg>Login</span>
    </nav>
    <h1 class="abs app-title">KRVcrate <em>Application</em></h1>
  </header>

  <div class="abs navbar"></div>
  <span class="abs nav-item" style="left:393px">INFO</span>
  <span class="abs nav-item active" style="left:464px">MENU <svg width="7" height="7" viewBox="0 0 7 7"><path d="M1 1l2.5 2.5L6 1M1 3.5 3.5 6 6 3.5" fill="none" stroke="#1a86d0" stroke-width="1.1"/></svg></span>
  <span class="abs nav-item" style="left:542px">ADMINISTRATOR <svg width="7" height="7" viewBox="0 0 7 7"><path d="M1 1l2.5 2.5L6 1M1 3.5 3.5 6 6 3.5" fill="none" stroke="#444" stroke-width="1.1"/></svg></span>
  <span class="abs nav-item" style="left:676px">SEARCH</span>
  <div class="abs search"><span>Search...</span><i><svg width="11" height="11" viewBox="0 0 11 11"><circle cx="4.5" cy="4.5" r="3.4" fill="none" stroke="#1a86d0" stroke-width="1.6"/><path d="M7 7l3 3" stroke="#1a86d0" stroke-width="1.8"/></svg></i></div>

  <aside>
    <div class="abs sidebar"></div>
    <div class="abs panel-head" style="top:170px">
      <svg width="16" height="16" viewBox="0 0 16 16"><rect x="0" y="0" width="16" height="7" fill="#f5a623"/><rect x="0" y="9" width="7" height="7" fill="#e2552c"/><rect x="9" y="9" width="7" height="7" fill="#8cc63f"/></svg>Explorador
    </div>
    <div class="abs tree-rail"></div>
    <ul class="abs tree">
      <li><svg width="28" height="10" viewBox="0 0 28 10"><rect x="0.5" y="0.5" width="8" height="8" fill="#fff" stroke="#999"/><path d="M2.5 4.5h4M4.5 2.5v4" stroke="#1a86d0"/><path d="M13 2h4l1 1.5h8V9H13z" fill="#f7c85a" stroke="#d8a12a"/></svg>administrator</li>
      <li><svg width="28" height="10" viewBox="0 0 28 10"><rect x="0.5" y="0.5" width="8" height="8" fill="#fff" stroke="#999"/><path d="M2.5 4.5h4M4.5 2.5v4" stroke="#1a86d0"/><path d="M13 2h4l1 1.5h8V9H13z" fill="#f7c85a" stroke="#d8a12a"/></svg>Clients</li>
      <li><svg width="28" height="10" viewBox="0 0 28 10"><rect x="0.5" y="0.5" width="8" height="8" fill="#fff" stroke="#999"/><path d="M2.5 4.5h4M4.5 2.5v4" stroke="#1a86d0"/><path d="M13 2h4l1 1.5h8V9H13z" fill="#f7c85a" stroke="#d8a12a"/></svg>Dep. Information</li>
      <li><svg width="28" height="10" viewBox="0 0 28 10"><rect x="0.5" y="0.5" width="8" height="8" fill="#fff" stroke="#999"/><path d="M2.5 4.5h4M4.5 2.5v4" stroke="#1a86d0"/><path d="M13 2h4l1 1.5h8V9H13z" fill="#f7c85a" stroke="#d8a12a"/></svg>Reclamacoes</li>
      <li><svg width="28" height="10" viewBox="0 0 28 10"><rect x="0.5" y="0.5" width="8" height="8" fill="#fff" stroke="#999"/><path d="M2.5 4.5h4M4.5 2.5v4" stroke="#1a86d0"/><path d="M13 2h4l1 1.5h8V9H13z" fill="#f7c85a" stroke="#d8a12a"/></svg>administrator</li>
      <li><svg width="28" height="10" viewBox="0 0 28 10"><rect x="0.5" y="0.5" width="8" height="8" fill="#fff" stroke="#999"/><path d="M2.5 4.5h4M4.5 2.5v4" stroke="#1a86d0"/><path d="M13 2h4l1 1.5h8V9H13z" fill="#f7c85a" stroke="#d8a12a"/></svg>Clients</li>
      <li><svg width="28" height="10" viewBox="0 0 28 10"><rect x="0.5" y="0.5" width="8" height="8" fill="#fff" stroke="#999"/><path d="M2.5 4.5h4M4.5 2.5v4" stroke="#1a86d0"/><path d="M13 2h4l1 1.5h8V9H13z" fill="#f7c85a" stroke="#d8a12a"/></svg>Dep. Information</li>
      <li><svg width="28" height="10" viewBox="0 0 28 10"><rect x="0.5" y="0.5" width="8" height="8" fill="#fff" stroke="#999"/><path d="M2.5 4.5h4M4.5 2.5v4" stroke="#1a86d0"/><path d="M13 2h4l1 1.5h8V9H13z" fill="#f7c85a" stroke="#d8a12a"/></svg>Reclamacoes</li>
    </ul>
    <div class="abs panel-head" style="top:470px">
      <svg width="17" height="15" viewBox="0 0 17 15"><path d="M8.5 1 16 14H1z" fill="#f5c400" stroke="#d59b00"/><path d="M8.5 5v5" stroke="#333" stroke-width="1.6"/><circle cx="8.5" cy="12" r=".9" fill="#333"/></svg>Alertas
    </div>
    <p class="abs empty-note">No existem alertas</p>
    <div class="abs note-rule"></div>
  </aside>

  <main>
    <div class="abs crumb"><svg width="13" height="10" viewBox="0 0 13 10"><path d="M.5 1.5h4l1 1.5h6V9H.5z" fill="none" stroke="#e3a22a"/></svg>ADMINISTRATOR / DEP. INFORMATION</div>

    <div class="abs bar" style="top:222px">Pesquisa<b></b></div>

    <span class="abs label" style="top:266px">#</span>
    <div class="abs select" style="left:458px;top:264px;width:67px">=<svg class="arrows" width="6" height="9" viewBox="0 0 6 9"><path d="M0 3.5 3 .5 6 3.5M0 5.5l3 3 3-3" fill="#444"/></svg></div>
    <div class="abs field" style="left:533px;top:264px;width:193px"></div>

    <span class="abs label" style="top:293px">Tipo</span>
    <div class="abs select" style="left:458px;top:291px;width:150px">Choose one<svg class="arrows" width="6" height="9" viewBox="0 0 6 9"><path d="M0 3.5 3 .5 6 3.5M0 5.5l3 3 3-3" fill="#444"/></svg></div>

    <span class="abs label" style="top:320px">Data Entrda</span>
    <div class="abs select" style="left:458px;top:319px;width:67px">=<svg class="arrows" width="6" height="9" viewBox="0 0 6 9"><path d="M0 3.5 3 .5 6 3.5M0 5.5l3 3 3-3" fill="#444"/></svg></div>
    <div class="abs field" style="left:533px;top:319px;width:193px"></div>

    <span class="abs label" style="top:348px">Comentario</span>
    <div class="abs select" style="left:458px;top:346px;width:67px">Contem<svg class="arrows" width="6" height="9" viewBox="0 0 6 9"><path d="M0 3.5 3 .5 6 3.5M0 5.5l3 3 3-3" fill="#444"/></svg></div>
    <div class="abs field" style="left:533px;top:346px;width:193px"></div>

    <div class="abs bar" style="top:403px">Pesquisa Avancada<b></b></div>

    <div class="abs select" style="left:355px;top:441px;width:150px">16 itens por pagina<svg class="arrows" width="6" height="9" viewBox="0 0 6 9"><path d="M0 3.5 3 .5 6 3.5M0 5.5l3 3 3-3" fill="#444"/></svg></div>
    <div class="abs pager" style="left:576px;top:441px"><span class="pg-btn"><svg width="5" height="7"><path d="M5 0v7L0 3.5z" fill="#444"/></svg></span>1 of 1<span class="pg-btn"><svg width="5" height="7"><path d="M0 0v7l5-3.5z" fill="#444"/></svg></span></div>
    <div class="abs pager" style="left:777px;top:441px">Pagina&nbsp;&nbsp;#<span class="field" style="width:40px;display:block"></span><span class="pg-btn go" style="width:18px;margin-left:2px">Ir!</span></div>

    <table class="abs grid">
      <thead>
        <tr>
          <th style="width:48px"># <i></i></th>
          <th style="width:75px">Tipo <i></i></th>
          <th style="width:94px">Data Entrada <i></i></th>
          <th style="width:121px">Comentarlo <i></i></th>
          <th style="width:54px">Cixa <i></i></th>
          <th></th><th></th><th></th><th></th><th style="border-right:0"></th>
        </tr>
      </thead>
      <tbody>
        <tr>
          <td>1</td><td>Requerimentos</td><td>03-06-2013</td><td></td><td></td>
          <td class="tool"><svg width="16" height="18" viewBox="0 0 16 18"><path d="M2 .5h8l4 4v13H2z" fill="#fff" stroke="#999"/><rect x="0" y="9" width="13" height="6" fill="#d8261c"/></svg></td>
          <td class="tool"><svg width="16" height="18" viewBox="0 0 16 18"><rect x="1.5" y="1.5" width="11" height="15" fill="#fff" stroke="#999"/><path d="M4 5h6M4 8h6M4 11h4" stroke="#888"/><path d="M9 14l6-6" stroke="#e8a12a" stroke-width="2"/></svg></td>
          <td class="tool"><svg width="16" height="18" viewBox="0 0 16 18"><rect x="1.5" y="1.5" width="10" height="14" fill="#fff" stroke="#999"/><path d="M3.5 5h6M3.5 8h6" stroke="#6aa0d8"/><circle cx="12" cy="13" r="3.5" fill="#d8261c"/><path d="M10 13h4" stroke="#fff"/></svg></td>
          <td class="tool"><svg width="18" height="18" viewBox="0 0 18 18"><circle cx="9" cy="10" r="7" fill="#fff" stroke="#e2552c" stroke-width="2"/><path d="M9 6v4l3 2" stroke="#333" fill="none"/></svg></td>
          <td class="tool"><svg width="16" height="18" viewBox="0 0 16 18"><rect x="3" y="1" width="11" height="11" fill="#1a86d0"/><rect x="1" y="5" width="11" height="11" fill="#e0245e"/></svg></td>
        </tr>
      </tbody>
    </table>

    <div class="abs select" style="left:355px;top:540px;width:150px">16 itens por pagina<svg class="arrows" width="6" height="9" viewBox="0 0 6 9"><path d="M0 3.5 3 .5 6 3.5M0 5.5l3 3 3-3" fill="#444"/></svg></div>
    <div class="abs pager" style="left:576px;top:540px"><span class="pg-btn"><svg width="5" height="7"><path d="M5 0v7L0 3.5z" fill="#444"/></svg></span>1 of 1<span class="pg-btn"><svg width="5" height="7"><path d="M0 0v7l5-3.5z" fill="#444"/></svg></span></div>
    <div class="abs pager" style="left:777px;top:540px">Pagina&nbsp;&nbsp;#<span class="field" style="width:40px;display:block"></span><span class="pg-btn go" style="width:18px;margin-left:2px">Ir!</span></div>
  </main>

  <div class="abs dropdown">
    <div>Adicionar Documento</div>
    <div>Ver Documentos WorkFlow</div>
    <div>Ver Alertas</div>
  </div>

  <footer>
    <div class="abs footer"></div>
    <div class="abs email">Ente your email</div>
    <div class="abs send">SEND NOW</div>
    <div class="abs vrule" style="left:405px"></div>
    <div class="abs call">Call us: <strong>(555) 014 2277</strong></div>
    <div class="abs vrule" style="left:697px"></div>
    <span class="abs social focus" style="left:748px"></span>
    <span class="abs social" style="left:784px"></span>
    <span class="abs social" style="left:820px"></span>
    <span class="abs social" style="left:856px"><svg width="25" height="25" viewBox="0 0 25 25"><rect x="6.5" y="8" width="12" height="9" fill="none" stroke="#444" stroke-width="1.4"/><path d="M6.5 8l6 5 6-5" fill="none" stroke="#444" stroke-width="1.4"/></svg></span>
    <div class="abs foot-rule"></div>
    <nav class="abs foot-links"><span>Home</span><span>About</span><span>Product</span><span>Services</span><span>Demo</span><span>Pricing</span><span>FAQ</span><span>Contact</span></nav>
    <p class="abs copyright">Copyright © 2013 KRVcrate. All Rights Reserved.</p>
  </footer>

</div>
</body>
</html>
```